Mortgage and Asset Finance Broker Needs a Wordpress Website Design

I need a modern looking Wordpress website to showcase my service as a mortgage and asset broker. I have a company and we work with various lenders to arrange mortgages, as well as commercial lending and business asset finance. The website needs to look professional, be easy to navigate and capture leads. SEO is obviously very important to me. It really needs to be something that shows trust and professioanlism.
Updates

On the home page I will need to have some boxes for Home Loans, Refinancing, Business (and Agriculture) Loans etc. I'd like a carousel in the middle which shows our lenders (so that can have the banks logos added).

It needs to be easy top navigate and showcase all we do - Home Loans, Refinancing, Commercial Loans, Car Loans, Asset Finance etc.

There are plenty of companies on the internet that do this.

There is some good information here https://lendplatehq.com.au/mortgage-broker-homepage/

I need to make sure that editing the website is easy (I think Wordpress has something that allows that).

Also we are very much an Australian business so that is something to advertise.

Industry/Entity Type

Mortgage and Finance Broker

Coding

Coded - Design and coding required

Number of Pages Required

5+ page

Requirements
Must have
• Easy to navigate professional feel. Must be responsive and mobile friendly.
Nice to have
• Homepage with links to inner pages. Contact buttons.

```html
<!DOCTYPE html>
<html lang="en">
<head>
<meta charset="utf-8">
<title>Nexora Financial Services – Home Loans for Temporary &amp; Non Residents</title>
<link href="https://fonts.googleapis.com/css2?family=Poppins:wght@400;500;600;700&display=swap" rel="stylesheet">
<style>
:root{
  --blue:#1461ad;
  --purple:#7a3a8c;
  --pink:#e5246b;
  --orange:#f7941d;
  --ink:#1b1b1b;
  --muted:#555;
  --grey:#f4f4f6;
  --black:#111;
  --white:#fff;
}
*{margin:0;padding:0;box-sizing:border-box}
html,body{width:1200px;height:3950px;overflow:hidden}
body{font-family:'Poppins',sans-serif;color:var(--ink);background:var(--white);position:relative}
.abs{position:absolute}
a{color:inherit;text-decoration:none}
.pink{color:var(--pink)}

/* top bar */
.topbar{left:0;top:0;width:1200px;height:41px;background:var(--blue);color:var(--white);font-size:13px;font-weight:600}
.topbar .enquire{left:0;top:0;width:600px;height:41px;background:var(--purple);clip-path:polygon(0 0,100% 0,96% 100%,0 100%);padding:9px 0 0 110px}
.topbar .contact{right:110px;top:10px;display:flex;gap:40px}
.topbar .contact span{display:flex;align-items:center;gap:6px}

/* header */
.header{left:0;top:41px;width:1200px;height:100px;background:var(--white)}
.brand-tab{left:107px;top:41px;width:258px;height:119px;background:var(--white);z-index:3;display:flex;align-items:center;gap:10px;padding-left:10px}
.brand-mark{width:34px;height:34px;border-radius:50%;background:var(--purple)}
.brand-name{font-size:30px;font-weight:700;line-height:1}
.brand-name small{display:block;font-size:11px;font-weight:600;letter-spacing:.5px;margin-top:4px}
.nav{top:84px;left:510px;display:flex;gap:21px;font-size:14px;font-weight:500}
.nav .active{color:var(--orange)}

/* hero */
.hero-bg{left:0;top:141px;width:1200px;height:550px;background:linear-gradient(100deg,#c9d8f5 0%,#f3dcf3 35%,#f0d6ef 55%,#e6c8df 75%,#b9a6c8 100%)}
.hero-photo{left:660px;top:141px;width:540px;height:550px;background:linear-gradient(180deg,rgba(210,170,160,.35),rgba(120,110,150,.55))}
.hero-title{left:110px;top:236px;width:560px;font-size:39px;line-height:49px;font-weight:700;text-transform:uppercase}
.hero-sub{left:110px;top:454px;width:460px;font-size:20px;line-height:29px;font-weight:500}
.btn{background:var(--blue);color:var(--white);font-size:12px;font-weight:700;text-transform:uppercase;border-radius:30px;display:flex;align-items:center;justify-content:center;gap:6px}
.btn svg{width:11px;height:11px}

/* services */
.svc{top:762px;width:236px;height:153px;background:var(--white);border-radius:60px;box-shadow:0 6px 22px rgba(0,0,0,.08);text-align:center}
.svc .icon{position:absolute;left:72px;top:-36px;width:92px;height:92px;border-radius:50%;border:6px solid #e6ecf6;display:flex;align-items:center;justify-content:center}
.svc .icon svg{width:42px;height:42px}
.svc h3{position:absolute;left:0;top:76px;width:100%;font-size:15px;font-weight:600;text-transform:uppercase}
.svc a{position:absolute;left:0;top:112px;width:100%;font-size:14px;text-decoration:underline}
.arrow{top:822px;font-size:22px;color:#333}

/* split sections */
.photo-pair{display:flex;gap:6px}
.photo-pair div{flex:1;border-radius:4px}
.center-badge{width:82px;height:82px;background:var(--white);display:flex;align-items:center;justify-content:center}
.center-badge span{width:40px;height:40px;background:var(--purple);border-radius:4px}
.section-title{font-size:30px;line-height:40px;font-weight:700;text-transform:uppercase}
.copy p{font-size:14px;line-height:24.5px;color:var(--muted);margin-bottom:16px}

/* lenders */
.lenders{left:0;top:1978px;width:1200px;height:330px;background:linear-gradient(135deg,#1058a6,#0d4c92 60%,#1461ad)}
.lenders-title{left:0;top:2043px;width:1200px;text-align:center;color:var(--white);font-size:30px;font-weight:700}
.lender{top:2117px;width:192px;height:102px;background:var(--white);border-radius:5px;display:flex;align-items:center;justify-content:center}
.lender span{width:60px;height:60px;border-radius:10px;background:#2b2b2b}

/* summary */
.summary-title{left:0;top:2374px;width:1200px;text-align:center;font-size:30px;font-weight:700}
.point{left:268px;width:664px;height:70px;background:var(--white);box-shadow:0 4px 16px rgba(0,0,0,.06);font-size:19px;font-weight:600;padding:22px 0 0 37px}
.point.hl{background:var(--purple);color:var(--white)}
.dots{border:1.5px dotted var(--blue)}

/* testimonials */
.grey{left:0;top:3028px;width:1200px;height:567px;background:var(--grey)}
.t-title{left:0;top:3106px;width:1200px;text-align:center;font-size:30px;font-weight:700}
.tcard{top:3197px;width:334px;height:187px;background:var(--white);border-radius:6px;box-shadow:0 4px 14px rgba(0,0,0,.05)}
.tcard .avatar{position:absolute;left:26px;top:-25px;width:62px;height:62px;border-radius:50%;background:linear-gradient(#d9d3cc,#9c8f84);border:3px solid var(--white)}
.tcard .who{position:absolute;left:104px;top:12px;font-size:12px;font-weight:700;display:flex;gap:14px}
.tcard .who b{color:var(--orange);letter-spacing:1px}
.tcard p{position:absolute;left:26px;top:50px;width:290px;font-size:13px;line-height:22px;color:#666;text-align:justify}

/* cta + footer */
.footer{left:0;top:3595px;width:1200px;height:355px;background:var(--black)}
.cta{left:127px;top:3448px;width:946px;height:261px;background:linear-gradient(135deg,#7d3b8f,#6c3280);color:var(--white);text-align:center}
.cta h2{margin-top:48px;font-size:31px;font-weight:700;text-transform:uppercase}
.cta p{margin:20px auto 0;width:600px;font-size:14px;line-height:26px}
.foot-brand{left:110px;top:3790px;display:flex;align-items:center;gap:10px;color:var(--white)}
.foot-nav{left:446px;top:3786px;display:flex;gap:21px;font-size:14px;font-weight:600;color:var(--white)}
.foot-line{left:410px;top:3818px;width:690px;height:1px;background:#333}
.foot-contact{left:446px;top:3836px;display:flex;gap:48px;font-size:14px;font-weight:600;color:var(--white)}
.foot-contact span{display:flex;align-items:center;gap:6px}
.copyright{left:410px;top:3893px;width:610px;text-align:center;font-size:11px;color:var(--white)}
</style>
</head>
<body>

<div class="abs topbar">
  <div class="abs enquire">ENQUIRE NOW</div>
  <div class="abs contact">
    <span><svg width="12" height="12" viewBox="0 0 12 12"><rect x="1" y="2" width="10" height="8" fill="none" stroke="#fff" stroke-width="1.4"/><path d="M1 2l5 4 5-4" fill="none" stroke="#fff" stroke-width="1.2"/></svg>info@nexorafinance.com</span>
    <span><svg width="12" height="12" viewBox="0 0 12 12"><rect x="0.5" y="0.5" width="11" height="11" rx="2" fill="#fff"/><path d="M3.5 3c.5 2.6 2.3 4.6 5 5.4l.8-1.2-1.5-.8-.7.7C5.9 6.6 5.2 5.9 4.9 4.7l.7-.7-.8-1.5z" fill="#1461ad"/></svg>CALL US &nbsp;+61 (02) 5550 0142</span>
  </div>
</div>

<div class="abs header"></div>
<div class="abs brand-tab">
  <span class="brand-mark"></span>
  <div class="brand-name">nexora<small>FINANCIAL SERVICES</small></div>
</div>
<nav class="abs nav">
  <a class="active">HOME</a><a>FREE REPORT</a><a>HOME LOANS</a><a>REVIEWS</a><a>ABOUT</a><a>BLOG</a><a>CONTACT</a>
</nav>

<section class="abs hero-bg" role="img" aria-label="Soft-focus suburban house in pink and lavender tones"></section>
<div class="abs hero-photo" role="img" aria-label="Smiling family of three, father carrying daughter on his back"></div>
<h1 class="abs hero-title">Australia’s leading<br>home loan experts for<br><span class="pink">temporary &amp; non<br>residents</span></h1>
<p class="abs hero-sub">Get Fast Home Loan Approval, At A Great Rate… <span class="pink">Even If You Don’t Have A 20% Deposit</span></p>
<a class="abs btn" style="left:112px;top:542px;width:276px;height:45px">Book free strategy session <svg viewBox="0 0 12 12"><circle cx="6" cy="6" r="6" fill="#fff"/><path d="M5 3.5 7.5 6 5 8.5" stroke="#1461ad" stroke-width="1.6" fill="none"/></svg></a>

<div class="abs arrow" style="left:43px">«</div>
<div class="abs arrow" style="left:1140px">»</div>
<div class="abs svc" style="left:87px">
  <div class="icon" style="background:var(--blue)"><svg viewBox="0 0 40 40"><path d="M6 19 20 7l14 12M10 16v16h20V16M17 32v-9h6v9" fill="none" stroke="#fff" stroke-width="2.2" stroke-linejoin="round"/></svg></div>
  <h3>Home Loans</h3><a>View More</a>
</div>
<div class="abs svc" style="left:349px">
  <div class="icon" style="background:var(--pink)"><svg viewBox="0 0 40 40"><rect x="8" y="6" width="14" height="26" fill="none" stroke="#fff" stroke-width="2"/><rect x="22" y="14" width="10" height="18" fill="none" stroke="#fff" stroke-width="2"/><path d="M12 11h6M12 16h6M12 21h6" stroke="#fff" stroke-width="2"/></svg></div>
  <h3>Commercial Loans</h3><a>View More</a>
</div>
<div class="abs svc" style="left:613px">
  <div class="icon" style="background:var(--orange)"><svg viewBox="0 0 40 40"><path d="M7 24l3-9h20l3 9v7H7z" fill="none" stroke="#fff" stroke-width="2.2" stroke-linejoin="round"/><path d="M7 24h26" stroke="#fff" stroke-width="2"/><circle cx="12" cy="28" r="1.8" fill="#fff"/><circle cx="28" cy="28" r="1.8" fill="#fff"/></svg></div>
  <h3>Car Loans</h3><a>View More</a>
</div>
<div class="abs svc" style="left:875px">
  <div class="icon" style="background:var(--purple)"><svg viewBox="0 0 40 40"><path d="M6 22l8-6 6 3 6-3 8 6-9 8-5-3-5 3z" fill="none" stroke="#fff" stroke-width="2" stroke-linejoin="round"/><path d="M14 12 20 7l6 5" fill="none" stroke="#fff" stroke-width="2"/></svg></div>
  <h3>Buisness Loans</h3><a>View More</a>
</div>

<div class="abs photo-pair" style="left:113px;top:1002px;width:410px;height:411px">
  <div role="img" aria-label="Woman working on a laptop" style="background:linear-gradient(160deg,#d9cfc5,#8c7b6e)"></div>
  <div role="img" aria-label="Man reviewing loan documents" style="background:linear-gradient(160deg,#bfb6ad,#6d655f)"></div>
</div>
<div class="abs center-badge" style="left:277px;top:1180px"><span></span></div>
<h2 class="abs section-title" style="left:628px;top:1008px;width:470px">When <span class="pink">temporary or non residents need finance</span> for residential property,here’s why they turn to Nexora…</h2>
<div class="abs copy" style="left:628px;top:1185px;width:450px">
  <p>Lorem ipsum dolor sit amet, consectetur adipiscing elit, sed do eiusmod tempor incididunt ut labore et dolore magna aliqua. Ut enim ad minim veniam, quis nostrud exercitation ullamco laboris nisi ut aliquip ex ea commodo consequat.</p>
  <p>Lorem ipsum dolor sit amet, consectetur adipiscing elit, sed do eiusmod tempor incididunt ut labore et dolore magna aliqua. Ut enim ad minim veniam, quis nostrud exercitation ullamco laboris nisi ut aliquip ex ea commodo consequat.</p>
</div>

<h2 class="abs section-title" style="left:113px;top:1523px;width:460px">How we <span class="pink">fast-track your home loan</span> approval</h2>
<div class="abs copy" style="left:113px;top:1620px;width:450px">
  <p>Lorem ipsum dolor sit amet, consectetur adipiscing elit, sed do eiusmod tempor incididunt ut labore et dolore magna aliqua. Ut enim ad minim veniam, quis nostrud exercitation ullamco laboris nisi ut aliquip ex ea commodo consequat.</p>
  <p>Lorem ipsum dolor sit amet, consectetur adipiscing elit, sed do eiusmod tempor incididunt ut labore et dolore magna aliqua. Ut enim ad minim veniam, quis nostrud exercitation ullamco laboris nisi ut aliquip ex ea commodo consequat.</p>
</div>
<div class="abs photo-pair" style="left:674px;top:1482px;width:409px;height:412px">
  <div role="img" aria-label="Father hugging his daughter at home" style="background:linear-gradient(160deg,#e3ddd5,#a1968a)"></div>
  <div role="img" aria-label="Smiling couple in their new home" style="background:linear-gradient(160deg,#ddd5cb,#8f8175)"></div>
</div>
<div class="abs center-badge" style="left:838px;top:1658px"><span></span></div>

<section class="abs lenders" role="img" aria-label="Blue-tinted office background"></section>
<h2 class="abs lenders-title">OUR LENDERS</h2>
<div class="abs lender" style="left:106px"><span></span></div>
<div class="abs lender" style="left:305px"><span></span></div>
<div class="abs lender" style="left:504px"><span></span></div>
<div class="abs lender" style="left:703px"><span></span></div>
<div class="abs lender" style="left:903px"><span></span></div>

<h2 class="abs summary-title">IN SUMMARY, WE <span class="pink">ALLOW YOU TO…</span></h2>
<div class="abs dots" style="left:932px;top:2490px;width:44px;height:79px;border-left:none"></div>
<div class="abs dots" style="left:216px;top:2572px;width:52px;height:82px;border-right:none"></div>
<div class="abs dots" style="left:932px;top:2656px;width:44px;height:83px;border-left:none"></div>
<div class="abs dots" style="left:216px;top:2740px;width:52px;height:80px;border-right:none"></div>
<div class="abs point" style="top:2449px">Secure loan approval, even when other banks have said “no”</div>
<div class="abs point" style="top:2533px">Fast-track and streamline your property purchase</div>
<div class="abs point" style="top:2618px">Increase your borrowing capacity</div>
<div class="abs point hl" style="top:2702px">Minimise the deposit required</div>
<div class="abs point" style="top:2785px">Pay a lower interest rate</div>
<a class="abs btn" style="left:463px;top:2893px;width:274px;height:45px">Book free strategy session <svg viewBox="0 0 12 12"><circle cx="6" cy="6" r="6" fill="#fff"/><path d="M5 3.5 7.5 6 5 8.5" stroke="#1461ad" stroke-width="1.6" fill="none"/></svg></a>

<section class="abs grey"></section>
<h2 class="abs t-title">WHAT OUR <span class="pink">CLIENTS SAY</span></h2>
<div class="abs tcard" style="left:83px">
  <div class="avatar" role="img" aria-label="Client portrait"></div>
  <div class="who">JHON SMITH <b>★★★★★</b></div>
  <p>Lorem ipsum dolor sit amet, consectetur adipiscing elit, sed do eiusmod tempor incididunt ut labore et dolore magna aliqua. Ut enim ad minim veniam, quis nostrud exercitation ullamco laboris nisi</p>
</div>
<div class="abs tcard" style="left:432px">
  <div class="avatar" role="img" aria-label="Client portrait"></div>
  <div class="who">JHON SMITH <b>★★★★★</b></div>
  <p>Lorem ipsum dolor sit amet, consectetur adipiscing elit, sed do eiusmod tempor incididunt ut labore et dolore magna aliqua. Ut enim ad minim veniam, quis nostrud exercitation ullamco laboris nisi</p>
</div>
<div class="abs tcard" style="left:777px">
  <div class="avatar" role="img" aria-label="Client portrait"></div>
  <div class="who">JHON SMITH <b>★★★★★</b></div>
  <p>Lorem ipsum dolor sit amet, consectetur adipiscing elit, sed do eiusmod tempor incididunt ut labore et dolore magna aliqua. Ut enim ad minim veniam, quis nostrud exercitation ullamco laboris nisi</p>
</div>

<footer class="abs footer"></footer>
<div class="abs cta">
  <h2>Free home loan strategy session</h2>
  <p>Request an exploratory chat about your options and how to secure fast home loan approval, at a competitive rate – even if you don’t have a 20% deposit.</p>
</div>
<a class="abs btn" style="left:463px;top:3618px;width:274px;height:43px">Book free strategy session <svg viewBox="0 0 12 12"><circle cx="6" cy="6" r="6" fill="#fff"/><path d="M5 3.5 7.5 6 5 8.5" stroke="#1461ad" stroke-width="1.6" fill="none"/></svg></a>

<div class="abs foot-brand">
  <span class="brand-mark"></span>
  <div class="brand-name">nexora<small>FINANCIAL SERVICES</small></div>
</div>
<nav class="abs foot-nav"><a>HOME</a><a>FREE REPORT</a><a>HOME LOANS</a><a>REVIEWS</a><a>ABOUT</a><a>BLOG</a><a>CONTACT</a></nav>
<div class="abs foot-line"></div>
<div class="abs foot-contact">
  <span><svg width="12" height="12" viewBox="0 0 12 12"><rect x="1" y="2" width="10" height="8" fill="none" stroke="#fff" stroke-width="1.4"/><path d="M1 2l5 4 5-4" fill="none" stroke="#fff" stroke-width="1.2"/></svg>info@nexorafinance.com</span>
  <span><svg width="12" height="12" viewBox="0 0 12 12"><rect x="0.5" y="0.5" width="11" height="11" rx="2" fill="#fff"/><path d="M3.5 3c.5 2.6 2.3 4.6 5 5.4l.8-1.2-1.5-.8-.7.7C5.9 6.6 5.2 5.9 4.9 4.7l.7-.7-.8-1.5z" fill="#111"/></svg>+61 (02) 5550 0142</span>
  <span><svg width="11" height="14" viewBox="0 0 11 14"><path d="M5.5 13S1 7.8 1 5a4.5 4.5 0 0 1 9 0c0 2.8-4.5 8-4.5 8z" fill="#fff"/><circle cx="5.5" cy="5" r="1.6" fill="#111"/></svg>123, Loru ipsum Dolor, USA</span>
</div>
<div class="abs copyright">Copyright@2025.All Rights Reserved</div>

</body>
</html>
```